Business Card Re-Design/Update

We'd like to update out business cards. I've included our current "Style guide" which has the colour scheme of the organisation in it. I've also included the branding files with logos etc in them.

I've also included a copy of one of our existing cards so that you can see how ugly/dated they look. I'd like a fresh modern corporate look.

Target Market(s)

These are for our clients, potential clients, industry contacts - like all business cards

Contact Information for Business Card

Name
Position
Company Address - Level 1, 47 Fernby Street, Carlow Qld 4072
Direct Phone
mobile
Email
Website -www.korvalit.com.au
Logo

Colors

Designer to choose colors to be used in the design.

Requirements
Must have
• Main Logo
• Cards will need to be editable to be able to personalize them for each new employee.
Nice to have
• The MapOut, ShipWell, KeepSteady would be okay to have if they can be sensibly and professionally added to the look without detracting from the main imagery.
• Maybe they could go on the back of the card? will leave this to your creative discretion as to whether/where they fit.
Should not have
• Should not have decorative or script fonts

```html
<!DOCTYPE html>
<html lang="en">
<head>
<meta charset="utf-8">
<title>Korvalit Business Card</title>
<link rel="stylesheet" href="https://fonts.googleapis.com/css2?family=Roboto:wght@400;500;700&family=Roboto+Condensed:wght@400;700&display=swap">
<style>
  :root {
    --backdrop: #262626;
    --card-dark: #262425;
    --card-light: #f0f0f0;
    --brand-red: #cc1a22;
    --brand-red-deep: #b5141b;
    --text-light: #ffffff;
    --text-dark: #2b2b2b;
  }
  * { margin: 0; padding: 0; box-sizing: border-box; }
  html, body { width: 1200px; height: 960px; overflow: hidden; }
  body { background: var(--backdrop); position: relative; font-family: "Roboto Condensed", Arial, sans-serif; }

  .card { position: absolute; width: 598px; height: 343px; box-shadow: 0 4px 10px rgba(0,0,0,.45); overflow: hidden; }
  .card-front { left: 323px; top: 108px; background: var(--card-light); }
  .card-back { left: 320px; top: 493px; background: radial-gradient(ellipse at 50% 40%, #dd1f27 0%, var(--brand-red) 45%, var(--brand-red-deep) 100%); }

  .contact-panel { position: absolute; left: 0; top: 0; width: 262px; height: 100%; background: var(--card-dark); color: var(--text-light); padding: 60px 0 0 21px; }
  .divider { position: absolute; left: 264px; top: 0; width: 8px; height: 100%; background: var(--brand-red); }
  .divider::after { content: ""; position: absolute; left: 0; top: 70px; width: 8px; height: 203px;
    background: repeating-linear-gradient(135deg, #2d2d2d 0 2px, #d8d8d8 2px 4px); }

  .person-name { font-size: 21px; font-weight: 400; color: var(--brand-red); letter-spacing: .2px; line-height: 24px; text-transform: uppercase; }
  .person-role { font-size: 14.5px; line-height: 20px; }
  .address { font-size: 14.5px; line-height: 18px; margin-top: 17px; }
  .contact-list { list-style: none; margin-top: 9px; }
  .contact-list li { display: flex; align-items: center; font-family: "Roboto", Arial, sans-serif; font-size: 14px; height: 19px; }
  .contact-list svg { width: 12px; height: 12px; margin-right: 10px; fill: var(--brand-red); flex: none; }

  .brand { position: absolute; left: 308px; top: 148px; display: flex; align-items: center; }
  .brand-square { width: 40px; height: 40px; background: var(--brand-red); margin-right: 14px; }
  .brand-name { font-family: "Roboto", Arial, sans-serif; font-weight: 500; font-size: 34px; color: var(--text-dark); letter-spacing: -.5px; }

  .back-brand { position: absolute; left: 0; right: 0; top: 92px; display: flex; justify-content: center; align-items: center; }
  .back-brand .brand-square { width: 70px; height: 70px; background: var(--text-light); margin-right: 22px; }
  .back-brand .brand-name { color: var(--text-light); font-size: 58px; font-weight: 700; }

  .services { position: absolute; left: 0; right: 0; top: 276px; display: flex; justify-content: center; gap: 34px; }
  .service { display: flex; align-items: center; font-family: "Roboto", Arial, sans-serif; font-weight: 500; font-size: 26px; color: var(--text-light); letter-spacing: -.5px; }
  .service::before { content: ""; width: 22px; height: 22px; background: var(--text-light); margin-right: 8px; }
</style>
</head>
<body>
  <section class="card card-front">
    <div class="contact-panel">
      <h1 class="person-name">Mara Hartley</h1>
      <p class="person-role">Business Development Manager</p>
      <p class="address">Level 1, 47 Fernby Street<br>Carlow Qld 4072</p>
      <ul class="contact-list">
        <li><svg viewBox="0 0 12 12"><path d="M2.5 1l2 2-1 1.5c.8 1.6 2 2.8 3.5 3.5L8.5 7l2 2-1.5 2C4.5 10.5 1.5 7.5 1 3z"/></svg>+61 (0)7 5550 1420</li>
        <li><svg viewBox="0 0 12 12"><path d="M2.5 1l2 2-1 1.5c.8 1.6 2 2.8 3.5 3.5L8.5 7l2 2-1.5 2C4.5 10.5 1.5 7.5 1 3z"/></svg>+61 (0)7 5550 1436</li>
        <li><svg viewBox="0 0 12 12"><path d="M3 0h6v12H3zM4 1.5v8h4v-8z"/></svg>+61 (0)491 570 218</li>
        <li><svg viewBox="0 0 12 12"><path d="M3 1h6v3H3zM0 5h12v5h-2V8H2v2H0zM3 9h6v3H3z"/></svg>+61 (0)7 5550 1499</li>
        <li><svg viewBox="0 0 12 12"><path d="M0 2h12v1.2L6 7 0 3.2zM0 4.6l6 3.8 6-3.8V10H0z"/></svg>mhartley@korvalit.com.au</li>
        <li><svg viewBox="0 0 12 12"><circle cx="6" cy="6" r="5.5"/></svg>www.korvalit.com.au</li>
      </ul>
    </div>
    <div class="divider"></div>
    <div class="brand">
      <span class="brand-square"></span>
      <span class="brand-name">korvalit</span>
    </div>
  </section>

  <section class="card card-back">
    <div class="back-brand">
      <span class="brand-square"></span>
      <span class="brand-name">korvalit</span>
    </div>
    <div class="services">
      <span class="service">MapOut</span>
      <span class="service">ShipWell</span>
      <span class="service">KeepSteady</span>
    </div>
  </section>
</body>
</html>
```